Brook Refrigeration. Refrigeration and air conditioning specialists.

We need a website to promote our business. We would a modern simple design using the colours from our logo and black. We want it to be fun but proffesional.

Target Market(s)

Commercial

Number of Pages Required

4 page

Requirements
Must have
• Home Page, About Us, Services and Contact Us.
• 24/7 365 days service available.
• Brook Refrigeration's dedicated team specialises in commercial refrigeration and air conditioning equipment.
• Based in Joondalup, we cover Perth Metro and surrounding areas.
Nice to have
• KNOWLEDGE . EXPERIENCE . PASSION in bold.
• Our experienced and highly trained technicians provide extensive knowledge and exceptional skills for your commercial refrigeration and air conditioning requirements.
• Pictures of commercial refrigeration.
Should not have
• No mention of domestic services.

```html
<!DOCTYPE html>
<html lang="en">
<head>
<meta charset="utf-8">
<title>Brook Refrigeration — Services</title>
<link href="https://fonts.googleapis.com/css2?family=Lato:wght@400;700;900&display=swap" rel="stylesheet">
<style>
  :root {
    --lime: #93ef5c;
    --lime-deep: #6fcf3e;
    --plum: #2c1c4a;
    --plum-mid: #4a2e78;
    --ink: #222222;
    --body: #4a4a4a;
    --white: #ffffff;
    --steel: #b9bec4;
    --store: #4d5257;
  }
  * { box-sizing: border-box; margin: 0; padding: 0; }
  html, body { width: 699px; height: 1200px; overflow: hidden; background: var(--white); }
  body { font-family: 'Lato', sans-serif; color: var(--body); }
  .page { position: relative; width: 699px; height: 1200px; overflow: hidden; }

  /* Header */
  .brand { position: absolute; left: 43px; top: 14px; width: 110px; font-weight: 900; font-size: 15px; line-height: 17px; color: var(--lime-deep); text-transform: uppercase; }
  .follow { position: absolute; left: 436px; top: 12px; display: flex; align-items: center; gap: 7px; font-size: 8.5px; font-weight: 700; color: var(--plum); text-transform: uppercase; }
  .dot { width: 11px; height: 11px; border-radius: 50%; background: var(--plum); display: inline-block; }
  .phone { position: absolute; left: 553px; top: 10px; display: flex; align-items: center; gap: 6px; font-size: 13.5px; font-weight: 900; color: var(--plum); }
  .nav { position: absolute; top: 39px; left: 424px; display: flex; align-items: center; }
  .nav a { display: block; font-size: 8.8px; font-weight: 700; color: var(--ink); text-decoration: none; text-transform: uppercase; padding: 6px 12px; height: 21px; }
  .nav a.is-active { background: var(--lime); }

  /* Hero band */
  .hero { position: absolute; left: 0; top: 68px; width: 699px; height: 114px;
    background: linear-gradient(100deg, #7fd95a 0%, #5fb34a 30%, #4a5a4e 55%, #3a2f52 78%, #4b2d7a 100%);
    display: flex; align-items: center; justify-content: center; }
  .hero h1 { color: var(--white); font-size: 15.5px; font-weight: 700; letter-spacing: 0.3px; }

  /* Services */
  .photo { position: absolute; }
  .photo--fridges { left: 43px; top: 234px; width: 307px; height: 204px;
    background: linear-gradient(90deg, #c8ccd0 0%, #9ea4aa 45%, #80868c 100%);
    clip-path: polygon(0 0, 100% 0, 98% 100%, 0 100%); }
  .photo--ac { left: 350px; top: 438px; width: 306px; height: 204px;
    background: linear-gradient(180deg, #d9dde2 0%, #a9b2bb 50%, #8a8373 100%);
    clip-path: polygon(0 0, 100% 0, 100% 100%, 4.5% 100%); }
  .service { position: absolute; width: 290px; }
  .service h2 { font-size: 17.5px; font-weight: 900; color: var(--plum); text-transform: uppercase; line-height: 22px; }
  .service p { margin-top: 13px; font-size: 8.6px; line-height: 14px; color: var(--body); }
  .btn { display: inline-block; background: var(--lime); color: var(--ink); font-size: 8.6px; font-weight: 700; text-transform: uppercase; text-align: center; width: 88px; height: 26px; line-height: 26px; }
  .service .btn { margin-top: 20px; }
  .service--refrigeration { left: 362px; top: 255px; }
  .service--aircon { left: 43px; top: 466px; }

  /* Quick contact */
  .contact-band { position: absolute; left: 0; top: 688px; width: 699px; height: 374px; }
  .quick { position: absolute; left: 0; top: 752px; width: 699px; text-align: center; }
  .quick h2 { color: var(--white); font-size: 17px; font-weight: 900; text-transform: uppercase; }
  .field { position: absolute; background: var(--white); border-radius: 2px; font-size: 8.6px; color: var(--body); padding: 11px 9px; }
  .field--half { width: 210px; height: 29px; }
  .field--message { left: 132px; top: 874px; width: 436px; height: 78px; padding-top: 11px; }
  .submit { position: absolute; left: 306px; top: 971px; width: 88px; height: 27px; line-height: 27px; }

  /* Footer */
  .footer-brand { position: absolute; left: 43px; top: 1084px; width: 110px; font-weight: 900; font-size: 15px; line-height: 17px; color: var(--lime-deep); text-transform: uppercase; }
  .legal { position: absolute; left: 43px; top: 1130px; font-size: 7.4px; line-height: 14px; color: var(--body); }
  .footer-col { position: absolute; top: 1076px; font-size: 7.8px; color: var(--ink); }
  .footer-col h3 { font-size: 8.4px; font-weight: 700; color: var(--plum); text-transform: uppercase; margin-bottom: 9px; }
  .footer-col li { list-style: none; line-height: 19px; }
  .footer-col .addr { line-height: 12.5px; margin-bottom: 3px; }
  .footer-col .row { display: flex; align-items: center; gap: 10px; line-height: 16px; }
  .footer-col .row svg { width: 8px; height: 8px; }
  .socials { display: flex; gap: 8px; margin-top: 2px; }
</style>
</head>
<body>
<div class="page">

  <header>
    <div class="brand">Brook Refrigeration</div>
    <div class="follow">Follow us <span class="dot"></span><span class="dot"></span></div>
    <div class="phone">
      <svg width="10" height="10" viewBox="0 0 24 24" aria-hidden="true"><path fill="#2c1c4a" d="M6.6 10.8a15.1 15.1 0 0 0 6.6 6.6l2.2-2.2c.3-.3.7-.4 1-.2 1.1.4 2.3.6 3.6.6.6 0 1 .4 1 1V20c0 .6-.4 1-1 1A17 17 0 0 1 3 4c0-.6.4-1 1-1h3.5c.6 0 1 .4 1 1 0 1.3.2 2.5.6 3.6.1.3 0 .7-.2 1z"/></svg>
      1300-555-018
    </div>
    <nav class="nav">
      <a href="#">Home</a>
      <a href="#">About</a>
      <a href="#" class="is-active">Services</a>
      <a href="#">Contact</a>
    </nav>
  </header>

  <section class="hero"><h1>SERVICES</h1></section>

  <div class="photo photo--fridges" role="img" aria-label="Row of stainless steel commercial refrigerators"></div>
  <article class="service service--refrigeration">
    <h2>Commercial Refrigeration</h2>
    <p>Lorem ipsum dolor sit amet, consectetur adipiscing elit. In ut leo sit amet mauris pellentesque lobortis. Praesent vulputate dictum venenatis. Pellentesque habitant morbi tristique senectus et netus et malesuada fames ac turpis egestas. Quisque sodales, dolor non convallis condimentum, arcu diam feugiat ligula...</p>
    <a class="btn" href="#">Read more</a>
  </article>

  <article class="service service--aircon">
    <h2>Air Conditioning Equipment</h2>
    <p>Lorem ipsum dolor sit amet, consectetur adipiscing elit. In ut leo sit amet mauris pellentesque lobortis. Praesent vulputate dictum venenatis. Pellentesque habitant morbi tristique senectus et netus et malesuada fames ac turpis egestas. Quisque sodales, dolor non convallis condimentum, arcu diam feugiat ligula...</p>
    <a class="btn" href="#">Read more</a>
  </article>
  <div class="photo photo--ac" role="img" aria-label="Outdoor air conditioning condenser units lined up beside a building"></div>

  <svg class="contact-band" viewBox="0 0 699 374" role="img" aria-label="Supermarket aisle with refrigerated display cases, darkened">
    <defs>
      <linearGradient id="storeTone" x1="0" y1="0" x2="1" y2="1">
        <stop offset="0" stop-color="#3f4448"/>
        <stop offset="0.5" stop-color="#55595d"/>
        <stop offset="1" stop-color="#45494c"/>
      </linearGradient>
    </defs>
    <polygon points="0,40 699,0 699,340 0,374" fill="url(#storeTone)"/>
  </svg>
  <div class="quick"><h2>Quick Contact</h2></div>
  <div class="field field--half" style="left:132px; top:796px;">Name</div>
  <div class="field field--half" style="left:358px; top:796px;">Phone Name</div>
  <div class="field field--half" style="left:132px; top:835px;">Email Address</div>
  <div class="field field--half" style="left:358px; top:835px;">Company Name</div>
  <div class="field field--message">Message</div>
  <a class="btn submit" href="#">Submit</a>

  <footer>
    <div class="footer-brand">Brook Refrigeration</div>
    <div class="legal">Copyright © 2018 Brook Refrigeration Pty Ltd.<br>All Rights Reserved.<br>ABN 00 000 000 000.</div>

    <div class="footer-col" style="left:242px;">
      <h3>Site Map</h3>
      <ul><li>Home</li><li>About</li><li>Services</li><li>Contatct Us</li></ul>
    </div>

    <div class="footer-col" style="left:366px;">
      <h3>Contact Us</h3>
      <div class="addr">12 Lakeside Drive<br>Joondalup WA 6027</div>
      <div class="row"><svg viewBox="0 0 24 24" aria-hidden="true"><path fill="#222" d="M6.6 10.8a15.1 15.1 0 0 0 6.6 6.6l2.2-2.2c.3-.3.7-.4 1-.2 1.1.4 2.3.6 3.6.6.6 0 1 .4 1 1V20c0 .6-.4 1-1 1A17 17 0 0 1 3 4c0-.6.4-1 1-1h3.5c.6 0 1 .4 1 1 0 1.3.2 2.5.6 3.6.1.3 0 .7-.2 1z"/></svg>1-800-555-0142</div>
      <div class="row"><svg viewBox="0 0 24 24" aria-hidden="true"><path fill="#222" d="M2 5h20v14H2z"/><path fill="none" stroke="#fff" stroke-width="2" d="M2 6l10 7 10-7"/></svg>hello@brookrefrig.example</div>
      <div class="row"><svg viewBox="0 0 24 24" aria-hidden="true"><path fill="#222" d="M12 2a7 7 0 0 0-7 7c0 5 7 13 7 13s7-8 7-13a7 7 0 0 0-7-7zm0 9.5a2.5 2.5 0 1 1 0-5 2.5 2.5 0 0 1 0 5z"/></svg>Map Direction</div>
    </div>

    <div class="footer-col" style="left:528px;">
      <h3>Follow Us</h3>
      <div class="socials"><span class="dot"></span><span class="dot"></span></div>
    </div>
  </footer>

</div>
</body>
</html>
```